New Fun, Positive, energised looking Business Card Needed for High Achiever Coach

I am looking for a two sided full colour business card. I am self employed and have recently re branded my 1-2-1 work re-vitalising high achievers. My target client base for these cards is therefore high achievers - usually aged 40 -55, they are often entrepreneurs, CEO or work in banking and finance and 2/3 are male. I work with them on 90 day or 6 month coaching programs to help them live their success in a healthier, more sustainable and fulfiiled way. They pay for this privately so though they are corporate types the cards need not look 'corporate'. I want to portray the idea of transformation, vitality and re-connecting.
You can get a feel for the look I like on my new website: morvenlisk.co.uk
I want to use this logo with strapline (Re-Vitalising High Achievers) (I purchased off Logoharbor) and font/ colours (the turquoise and green).
Details to include on the card:
www.morvenlisk.co.uk
+44 7915 302618
morven@morvenlisk.co.uk
skype: morvenlisk
I'd also like to include:
Do you struggle to switch off? Want to be healthier and feel fitter? Want closer relationships? More clarity over the direction you are headed? I can help you do these things using integrated mind-body techniques. Visit morvenlisk.co.uk TODAY to apply for a FREE Breakthrough session.
BUT if that is too much text for a card I am open to advice/ammendments.
Updates
Thanks for your design - I am considering them. PLease change the wording to :

```html
<!DOCTYPE html>
<html lang="en">
<head>
<meta charset="utf-8">
<title>Morven Lisk – Business Card</title>
<link rel="stylesheet" href="https://fonts.googleapis.com/css2?family=Fredoka:wght@600&family=Open+Sans:ital,wght@0,400;0,700;1,400&display=swap">
<style>
  :root {
    --turquoise: #1ba5cc;
    --turquoise-dark: #1590b4;
    --green: #5cb85c;
    --ink: #3a3a3a;
    --paper: #ffffff;
    --tint: #eef5f1;
    --backdrop: #ececec;
  }
  * { box-sizing: border-box; margin: 0; padding: 0; }
  html, body { width: 1200px; height: 720px; overflow: hidden; }
  body {
    background: var(--backdrop);
    font-family: "Open Sans", Arial, sans-serif;
    display: flex;
    align-items: center;
    justify-content: center;
    gap: 40px;
  }
  .card {
    position: relative;
    width: 540px;
    height: 330px;
    overflow: hidden;
    border-radius: 4px;
    box-shadow: 0 6px 18px rgba(0,0,0,0.12);
  }
  /* Front */
  .card--front { background: var(--paper); }
  .card__decor {
    position: absolute;
    right: -70px;
    top: -40px;
    width: 300px;
    height: 300px;
  }
  .brand {
    position: absolute;
    left: 40px;
    top: 60px;
  }
  .brand__row { display: flex; align-items: center; gap: 12px; }
  .brand__dot { width: 34px; height: 34px; border-radius: 50%; background: var(--green); }
  .brand__name {
    font-family: "Fredoka", "Open Sans", sans-serif;
    font-weight: 600;
    font-size: 34px;
    color: var(--turquoise);
    line-height: 1;
  }
  .brand__strapline {
    margin-top: 6px;
    font-size: 14px;
    font-style: italic;
    color: var(--turquoise);
  }
  .contacts {
    position: absolute;
    left: 40px;
    top: 170px;
    list-style: none;
    font-size: 17px;
    color: var(--ink);
  }
  .contacts li { display: flex; align-items: center; gap: 9px; height: 29px; }
  .contacts svg { width: 16px; height: 16px; flex: none; }

  /* Back */
  .card--back { background: var(--turquoise); color: var(--paper); }
  .card--back .card__decor { left: 150px; right: auto; top: 30px; width: 260px; height: 260px; }
  .pitch {
    position: absolute;
    inset: 0;
    display: flex;
    flex-direction: column;
    justify-content: center;
    align-items: center;
    text-align: center;
    padding: 0 30px;
    font-size: 16.5px;
    line-height: 1.38;
  }
  .pitch p + p { margin-top: 10px; }
  .pitch strong { font-weight: 700; }
</style>
</head>
<body>

  <section class="card card--front" aria-label="Card front">
    <svg class="card__decor" viewBox="0 0 300 300" aria-hidden="true">
      <circle cx="150" cy="150" r="120" fill="none" stroke="var(--tint)" stroke-width="26"/>
    </svg>

    <div class="brand">
      <div class="brand__row">
        <span class="brand__dot"></span>
        <span class="brand__name">Morven Lisk</span>
      </div>
      <p class="brand__strapline">Re-Vitalising High Achievers</p>
    </div>

    <ul class="contacts">
      <li>
        <svg viewBox="0 0 16 16" aria-hidden="true"><circle cx="8" cy="8" r="7.5" fill="none" stroke="var(--ink)"/><path d="M5.5 4.5l1.5 0 .6 2-1 .8a5 5 0 0 0 2.1 2.1l.8-1 2 .6v1.5c-3.5.6-6.6-2.5-6-6z" fill="var(--ink)"/></svg>
        +44 7915 302618
      </li>
      <li>
        <svg viewBox="0 0 16 16" aria-hidden="true"><circle cx="8" cy="8" r="8" fill="var(--ink)"/><rect x="4" y="5.2" width="8" height="5.6" fill="none" stroke="#fff"/><path d="M4 5.2l4 3 4-3" fill="none" stroke="#fff"/></svg>
        morven@morvenlisk.co.uk
      </li>
      <li>
        <svg viewBox="0 0 16 16" aria-hidden="true"><circle cx="8" cy="8" r="8" fill="var(--ink)"/><circle cx="8" cy="8" r="4.5" fill="none" stroke="#fff"/><ellipse cx="8" cy="8" rx="2" ry="4.5" fill="none" stroke="#fff"/><path d="M3.5 8h9" stroke="#fff"/></svg>
        www.morvenlisk.co.uk
      </li>
      <li>
        <svg viewBox="0 0 16 16" aria-hidden="true"><circle cx="8" cy="8" r="8" fill="var(--ink)"/></svg>
        morvenlisk
      </li>
    </ul>
  </section>

  <section class="card card--back" aria-label="Card back">
    <svg class="card__decor" viewBox="0 0 260 260" aria-hidden="true">
      <circle cx="130" cy="130" r="105" fill="none" stroke="var(--turquoise-dark)" stroke-width="22" opacity="0.45"/>
    </svg>
    <div class="pitch">
      <p>Do you struggle to switch off?<br>
      Want to be healthier and feel fitter?<br>
      Want closer relationships?<br>
      More clarity over the direction you are headed?</p>
      <p>I can help you do these things using integrated<br>mind-body techniques.</p>
      <p>Visit <strong>morvenlisk.co.uk</strong> TODAY to apply for a<br>FREE Breakthrough session.</p>
    </div>
  </section>

</body>
</html>
```